Business Card Design Project

I require a business card with the following information on them for various different people;
name
m:
f:
e:
I have a logo already and will attached that. We are in the construction industry. I require something clean and simple but eye catching at the same time. You can use another colour with our logo if you like and you can style the logo as well if you wish. I am open.
Also it needs to be front and back design.
Industry/Entity Type
Construction
Requirements
Must have
- Logo, name, mobile, fax and email address.
Front and back design

```html
<!DOCTYPE html>
<html lang="en">
<head>
<meta charset="utf-8">
<title>Stonebridge Developments – Business Cards</title>
<link rel="stylesheet" href="https://fonts.googleapis.com/css2?family=Questrial&family=Arimo:wght@400;700&display=swap">
<style>
  :root {
    --backdrop: #262626;
    --card-white: #ffffff;
    --card-shade: #e9e9e9;
    --green-deep: #4daa2c;
    --green-light: #8dc63f;
    --text-dark: #3a3a3a;
    --text-white: #ffffff;
    --divider: rgba(255,255,255,0.55);
  }
  html, body {
    margin: 0;
    padding: 0;
    overflow: hidden;
  }
  body {
    width: 1200px;
    height: 944px;
    background: var(--backdrop);
    position: relative;
    font-family: "Arimo", Arial, sans-serif;
  }
  .card {
    position: absolute;
    width: 620px;
    height: 354px;
    border-radius: 24px;
    background: linear-gradient(160deg, var(--card-white) 55%, var(--card-shade) 100%);
    box-shadow: 0 10px 28px rgba(0,0,0,0.45);
    overflow: hidden;
  }
  .card--front { left: 90px; top: 100px; }
  .card--back  { left: 490px; top: 500px; }

  /* Front */
  .brand {
    position: absolute;
    left: 58px;
    top: 168px;
    display: flex;
    align-items: center;
    gap: 16px;
  }
  .brand__mark {
    width: 58px;
    height: 58px;
    background: var(--green-deep);
  }
  .brand__name {
    font-family: "Questrial", "Century Gothic", sans-serif;
    color: var(--green-deep);
    font-size: 40px;
    line-height: 1;
    margin: 0;
  }
  .brand__name span {
    display: block;
    font-size: 19px;
    letter-spacing: 5px;
    margin-top: 6px;
  }
  .front__web {
    position: absolute;
    left: 132px;
    top: 254px;
    font-weight: 700;
    font-size: 17px;
    letter-spacing: 2px;
    color: var(--text-dark);
    margin: 0;
  }

  /* Back */
  .band {
    position: absolute;
    left: 0;
    right: 0;
    top: 128px;
    height: 136px;
    display: flex;
    background: var(--green-light);
  }
  .band__person {
    width: 192px;
    background: var(--green-deep);
    color: var(--text-white);
    padding: 22px 0 0 38px;
    box-sizing: border-box;
  }
  .person__name {
    margin: 0;
    font-size: 22px;
    font-weight: 400;
  }
  .person__role {
    margin: 4px 0 0;
    font-size: 15px;
  }
  .band__divider {
    width: 1px;
    background: var(--divider);
    margin: 22px 0 52px 10px;
  }
  .band__contact {
    list-style: none;
    margin: 0;
    padding: 20px 0 0 22px;
    color: var(--text-white);
    font-size: 17px;
    line-height: 23px;
  }
</style>
</head>
<body>
  <section class="card card--front" aria-label="Business card front">
    <div class="brand">
      <div class="brand__mark"></div>
      <h1 class="brand__name">Stonebridge<span>DEVELOPMENTS</span></h1>
    </div>
    <p class="front__web">www.stonebridgedev.com</p>
  </section>

  <section class="card card--back" aria-label="Business card back">
    <div class="band">
      <div class="band__person">
        <h2 class="person__name">Mark Ellery</h2>
        <p class="person__role">manager</p>
      </div>
      <div class="band__divider"></div>
      <ul class="band__contact">
        <li>ph. 512-555-0142</li>
        <li>fax 512-555-0143</li>
        <li>info@stonebridgedev.com</li>
        <li>www.stonebridgedev.com</li>
      </ul>
    </div>
  </section>
</body>
</html>
```